RTavenor Business Cards & Letterhead

I have a logo but need a design for some new business cards. We are a Design-Build Firm that specializes in the design and construction of commercial projects.
the cards need to be professional. no cartoon stuff.
i would like to have the cards in AI format so I can update the card as needed. Logo is provided.
Our Address is: 4187 Marlowe Ct. Linwood Falls, Vermont 27614

```html
<!DOCTYPE html>
<html lang="en">
<head>
<meta charset="utf-8">
<title>RTavenor Business Card</title>
<link rel="stylesheet" href="https://fonts.googleapis.com/css2?family=Montserrat:wght@400;500;700;800&display=swap">
<style>
  :root {
    --page-bg: #d9d9d9;
    --blue-light: #5f9cc4;
    --blue-mid: #2f82b8;
    --blue-deep: #146aa3;
    --brand-blue: #2b74a8;
    --ink-grey: #58595b;
    --text-grey: #555;
    --band-grey: #616264;
    --card-white: #f3f3f3;
    --card-white-2: #e9e9e9;
    --icon-cut: #f0f0f0;
  }
  * { margin: 0; padding: 0; box-sizing: border-box; }
  html, body { width: 1200px; height: 1200px; overflow: hidden; }
  body {
    background: var(--page-bg);
    font-family: "Montserrat", sans-serif;
    display: flex;
    flex-direction: column;
    align-items: center;
    justify-content: center;
    gap: 60px;
  }
  .card {
    position: relative;
    width: 900px;
    height: 514px;
    border-radius: 34px;
    overflow: hidden;
  }
  .card-back {
    background: linear-gradient(115deg, var(--blue-light) 0%, var(--blue-mid) 45%, var(--blue-deep) 100%);
    display: flex;
    align-items: center;
    justify-content: center;
  }
  .card-back .wordmark {
    font-weight: 800;
    font-size: 96px;
    letter-spacing: 2px;
    color: #4a8fbd;
  }
  .card-front {
    background: linear-gradient(90deg, var(--card-white) 0%, var(--card-white-2) 100%);
  }
  .front-logo {
    position: absolute;
    top: 92px;
    left: 0;
    right: 0;
    display: flex;
    justify-content: center;
    align-items: center;
    gap: 14px;
  }
  .front-logo .mark-square {
    width: 34px;
    height: 34px;
    background: var(--brand-blue);
  }
  .front-logo .wordmark {
    font-weight: 800;
    font-size: 68px;
    letter-spacing: 1px;
    color: var(--ink-grey);
  }
  .holder {
    position: absolute;
    left: 70px;
    top: 292px;
  }
  .holder-name {
    font-weight: 800;
    font-size: 36px;
    color: var(--brand-blue);
  }
  .holder-title {
    font-weight: 400;
    font-size: 22px;
    color: var(--text-grey);
    margin-top: 4px;
    padding-left: 16px;
  }
  .contact-list {
    position: absolute;
    left: 530px;
    top: 236px;
    list-style: none;
  }
  .contact-list li {
    display: flex;
    align-items: center;
    gap: 14px;
    font-size: 22px;
    color: var(--text-grey);
    height: 36px;
  }
  .contact-list svg { width: 20px; height: 20px; fill: var(--brand-blue); flex: none; }
  .address-band {
    position: absolute;
    left: 0; right: 0; bottom: 0;
    height: 84px;
    background: var(--band-grey);
    color: #fff;
    font-size: 22px;
    font-weight: 500;
    display: flex;
    align-items: center;
    justify-content: center;
    letter-spacing: 0.3px;
  }
</style>
</head>
<body>
  <section class="card card-back">
    <span class="wordmark">RTAVENOR</span>
  </section>

  <section class="card card-front">
    <div class="front-logo">
      <span class="mark-square"></span>
      <span class="wordmark">RTAVENOR</span>
    </div>

    <div class="holder">
      <p class="holder-name">Ronan Tavenor</p>
      <p class="holder-title">President</p>
    </div>

    <ul class="contact-list">
      <li>
        <svg viewBox="0 0 24 24"><path d="M6.6 10.8a15.1 15.1 0 0 0 6.6 6.6l2.2-2.2a1 1 0 0 1 1-.25 11.4 11.4 0 0 0 3.6.57 1 1 0 0 1 1 1V20a1 1 0 0 1-1 1A17 17 0 0 1 3 4a1 1 0 0 1 1-1h3.5a1 1 0 0 1 1 1c0 1.25.2 2.45.57 3.57a1 1 0 0 1-.25 1z"/></svg>
        (555)-214-0147
      </li>
      <li>
        <svg viewBox="0 0 24 24"><path d="M2 5h20v14H2z"/><path d="M3 6l9 7 9-7" fill="none" stroke="var(--icon-cut)" stroke-width="1.6"/></svg>
        info@rtavenor.com
      </li>
      <li>
        <svg viewBox="0 0 24 24"><circle cx="12" cy="12" r="10"/><path d="M2 12h20M12 2c3 3 3 17 0 20M12 2c-3 3-3 17 0 20" fill="none" stroke="var(--icon-cut)" stroke-width="1.5"/></svg>
        www.rtavenor.com
      </li>
    </ul>

    <div class="address-band">4187 Marlowe Ct. Linwood Falls, Vermont 27614</div>
  </section>
</body>
</html>
```